Web Design Project

We are an IT System Integrator. We provide Korvin 450 ERP System, CRM etc. We also provide hardware, networking servicing. Please look at www.zolvantix.com.sg. They provide the same service as us. We like to redesign our web site. I will attached the color that I prefer for reference.

Our website is www.tadurk.com.sg.  It has been created about 14 years ago.  We are trying to revamp it with a new look and information.   The new website must be informative, fast.    I have attached an attachment which show the color that I prefer(brownish golden).   

Our competitor (www.zolvantix.com) is carrying the same trade as us.  They have all the informations In their website that we will like to have.  Therefore I recommend you to take a look at my competitor website and have a better   
understanding on the kind of information I would like to have for my new website.

This project is guarantee to the person with the best design.  We can have it guarantee.

Target Market(s)

Corporate and companies

Industry/Entity Type

Hardware

```html
<!DOCTYPE html>
<html lang="en">
<head>
<meta charset="utf-8">
<title>Tadurk Information Systems</title>
<link href="https://fonts.googleapis.com/css2?family=Arimo:wght@400;700&display=swap" rel="stylesheet">
<style>
:root{
  --bar-dark:#2f2f2f;
  --gold:#a68842;
  --gold-text:#9c7a30;
  --link-gold:#b8760a;
  --nav-ink:#3b2e10;
  --cream:#f5f1e6;
  --cream-edge:#e4d9c1;
  --panel:#f7f7f7;
  --ink:#2d2d2d;
  --body:#5a5a5a;
  --muted:#8a8a8a;
  --rule:#e6e6e6;
  --partner:#cfcfcf;
  --circle:#e2b544;
}
*{margin:0;padding:0;box-sizing:border-box}
html,body{width:1091px;height:1200px;overflow:hidden;background:#fff}
body{font-family:"Arimo",Arial,sans-serif;color:var(--ink)}
.page{position:relative;width:1200px;height:1320px;transform:scale(.909167);transform-origin:0 0}
.abs{position:absolute}
a{text-decoration:none;color:inherit}

.utility-bar{left:0;top:0;width:1200px;height:38px;background:var(--bar-dark)}
.utility-bar ul{list-style:none;position:absolute;right:103px;top:12px;display:flex;gap:22px;font-size:11.5px;color:#fff}

.masthead{left:0;top:38px;width:1200px;height:106px;background:var(--gold)}
.brand{left:96px;top:0;width:174px;height:106px;background:linear-gradient(135deg,#e9dcb8 0%,#b89a55 45%,var(--gold) 100%);display:flex;flex-direction:column;justify-content:center;padding-left:16px}
.brand-name{font-size:34px;font-weight:700;color:#4a360c;letter-spacing:1px;line-height:1}
.brand-sub{font-size:12px;color:#4a360c;margin-top:8px}
.main-nav{list-style:none;left:533px;top:0;height:106px;display:flex;font-size:12.5px;font-weight:700;color:var(--nav-ink)}
.main-nav li{height:106px;display:flex;align-items:center}
.main-nav .current{width:83px;justify-content:center;background:linear-gradient(#fbf7ee,#ece1c8 70%,#d7c49b)}
.main-nav .item{margin-left:30px}
.main-nav .item:first-of-type{margin-left:30px}

.hero{left:96px;top:144px;width:1000px;height:376px;background:linear-gradient(100deg,#e9e6e3 0%,#cfc7c2 30%,#f1eeea 55%,#d9d0c8 78%,#eeeae6 100%)}
.slider-dots{right:26px;bottom:21px;display:flex;gap:4px}
.slider-dots span{width:37px;height:4px;background:#fff}

.welcome{left:96px;top:520px;width:1000px;height:177px;background:var(--cream);border-bottom:3px solid var(--cream-edge)}
.welcome-photo{left:13px;top:18px;width:220px;height:135px;background:linear-gradient(120deg,#d8cfc6,#f0ece8 60%,#e2dcd5)}
.welcome h1{left:246px;top:20px;font-size:16px;font-weight:700;color:var(--gold-text)}
.welcome p{left:248px;top:52px;width:728px;font-size:13px;line-height:18px;color:var(--body)}
.welcome p a{color:var(--link-gold)}

.services{left:96px;top:697px;width:1001px;height:346px;background:var(--panel)}
.services h2{font-size:15.5px;font-weight:400;color:var(--ink);letter-spacing:.2px}
.products{left:25px;top:27px;width:540px}
.products p{margin-top:10px;font-size:12px;line-height:17px;color:var(--body);padding-left:2px}
.product-list{list-style:none;position:absolute;top:113px;font-size:13px;font-weight:700;color:var(--ink)}
.product-list li{display:flex;align-items:center;height:33px}
.product-list svg{margin-right:12px}
.list-a{left:13px}
.list-b{left:224px}

.highlights{left:625px;top:27px;width:360px}
.highlights h3{font-size:13px;font-weight:700;color:var(--ink);margin-top:17px;padding-left:1px}
.highlights h3.first{margin-top:17px}
.highlights p{margin-top:7px;font-size:12px;line-height:17px;color:var(--body);padding-left:3px}
.highlights .more{color:var(--link-gold)}

.partners{left:96px;top:1071px;width:1000px;height:101px;border-top:1px solid var(--rule);border-bottom:1px solid var(--rule)}

.footer-rule{left:96px;top:1196px;width:1000px;height:6px;background:var(--gold)}
.footer-nav{list-style:none;left:123px;top:1226px;display:flex;font-size:12.5px;font-weight:700;color:var(--ink)}
.footer-nav li{margin-right:26px}
.footer-nav li:first-child{margin-right:53px}
.legal{left:121px;top:1257px;font-size:12px;line-height:14px;color:var(--muted)}
.social{left:974px;top:1237px;display:flex;gap:7px}
.social span{width:31px;height:30px;border-radius:4px}
</style>
</head>
<body>
<div class="page">

  <nav class="utility-bar abs" aria-label="Utility">
    <ul>
      <li>SITEMAP</li><li>LOG-INCIDENT</li><li>ENQUIRY</li><li>CONTACT</li><li>CLIENT SUPPORT</li>
    </ul>
  </nav>

  <header class="masthead abs">
    <div class="brand abs">
      <span class="brand-name">TIS</span>
      <span class="brand-sub">Tadurk Information System</span>
    </div>
    <ul class="main-nav abs">
      <li class="current">HOME</li>
      <li class="item">COMPANY</li>
      <li class="item">PRODUCTS</li>
      <li class="item">KORVIN</li>
      <li class="item">SERVICES</li>
      <li class="item">CLIENTS</li>
      <li class="item">CAREERS</li>
    </ul>
  </header>

  <section class="hero abs" role="img" aria-label="Photo of a smiling businesswoman with colleagues meeting in a bright office">
    <div class="slider-dots abs"><span></span><span></span><span></span><span></span><span></span></div>
  </section>

  <section class="welcome abs">
    <div class="welcome-photo abs" role="img" aria-label="Photo of a cheerful woman in office attire"></div>
    <h1 class="abs">WELCOME TO TADURK</h1>
    <p class="abs">Tadurk Information Systems Pte Ltd (TIS) is professionally managed by a core group of visionaries and technologists with decades of industry experience between them and backed by a team of trained professionals at all levels of operations. Perfection is a way of life at TIS. The organization has grown from a small beginning in 1993, to become a company of international repute for reliability. TIS has transformed from an KORVIN Reseller to a company providing total IT solutions to companies in Singapore and the Asia region. TIS provides hardware maintenance, networking, software and consulting services. <a href="#">Read more..</a></p>
  </section>

  <section class="services abs">
    <div class="products abs">
      <h2>OUR PRODUCTS &amp; SERVICES</h2>
      <p>Sed ut perspiciatis unde omnis iste natus error sit voluptatem accusantium doloremque laudantium totam rem eaque ipsa quae ab illo inventore veritatis et quasi architecto beatae vitae dicta sunt explicabo. Nemo enim ipvoluptatem quia voluptas sit aspernatur aut odit aut</p>
    </div>
    <ul class="product-list list-a">
      <li><svg width="20" height="20" viewBox="0 0 20 20"><circle cx="10" cy="10" r="9" fill="#fff" stroke="var(--circle)"/><path d="M8.5 7l3 3-3 3" fill="none" stroke="var(--circle)" stroke-width="1.4"/></svg>Servers</li>
      <li><svg width="20" height="20" viewBox="0 0 20 20"><circle cx="10" cy="10" r="9" fill="#fff" stroke="var(--circle)"/><path d="M8.5 7l3 3-3 3" fill="none" stroke="var(--circle)" stroke-width="1.4"/></svg>Workstations</li>
      <li><svg width="20" height="20" viewBox="0 0 20 20"><circle cx="10" cy="10" r="9" fill="#fff" stroke="var(--circle)"/><path d="M8.5 7l3 3-3 3" fill="none" stroke="var(--circle)" stroke-width="1.4"/></svg>Printers</li>
      <li><svg width="20" height="20" viewBox="0 0 20 20"><circle cx="10" cy="10" r="9" fill="#fff" stroke="var(--circle)"/><path d="M8.5 7l3 3-3 3" fill="none" stroke="var(--circle)" stroke-width="1.4"/></svg>Surveillance Cameras</li>
    </ul>
    <ul class="product-list list-b">
      <li><svg width="20" height="20" viewBox="0 0 20 20"><circle cx="10" cy="10" r="9" fill="#fff" stroke="var(--circle)"/><path d="M8.5 7l3 3-3 3" fill="none" stroke="var(--circle)" stroke-width="1.4"/></svg>Servers</li>
      <li><svg width="20" height="20" viewBox="0 0 20 20"><circle cx="10" cy="10" r="9" fill="#fff" stroke="var(--circle)"/><path d="M8.5 7l3 3-3 3" fill="none" stroke="var(--circle)" stroke-width="1.4"/></svg>Workstations</li>
      <li><svg width="20" height="20" viewBox="0 0 20 20"><circle cx="10" cy="10" r="9" fill="#fff" stroke="var(--circle)"/><path d="M8.5 7l3 3-3 3" fill="none" stroke="var(--circle)" stroke-width="1.4"/></svg>Printers</li>
      <li><svg width="20" height="20" viewBox="0 0 20 20"><circle cx="10" cy="10" r="9" fill="#fff" stroke="var(--circle)"/><path d="M8.5 7l3 3-3 3" fill="none" stroke="var(--circle)" stroke-width="1.4"/></svg>Surveillance Cameras</li>
    </ul>

    <div class="highlights abs">
      <h2>OUR HIGHLIGHTS</h2>
      <h3 class="first">Technical Services</h3>
      <p>Sed ut perspiciatis unde omnis iste natus error sit voluptatem accusantium doloremque laudantium totam rem eaque ipsa quae ab illo inventore veritatis et</p>
      <h3>Custom Program Services</h3>
      <p>Sed ut perspiciatis unde omnis iste natus error sit voluptatem accusantium doloremque laudantium totam rem eaque ipsa quae ab illo inventore veritatis et</p>
      <h3>Training &amp; Solutions</h3>
      <p>Sed ut perspiciatis unde omnis iste natus error sit voluptatem accusantium.<br><a class="more" href="#">More Services</a></p>
    </div>
  </section>

  <section class="partners abs" aria-label="Partners">
    <svg width="1000" height="101" viewBox="0 0 1000 101">
      <rect x="34" y="28" width="148" height="44" rx="6" fill="var(--partner)"/>
      <rect x="285" y="20" width="72" height="56" rx="4" fill="var(--partner)"/>
      <circle cx="492" cy="48" r="40" fill="var(--partner)"/>
      <rect x="598" y="33" width="136" height="38" fill="var(--partner)"/>
      <rect x="792" y="28" width="166" height="50" rx="4" fill="var(--partner)"/>
    </svg>
  </section>

  <div class="footer-rule abs"></div>
  <ul class="footer-nav abs">
    <li>HOME</li><li>COMPANY</li><li>PRODUCTS</li><li>KORVIN</li><li>SERVICES</li><li>CLIENTS</li><li>CAREERS</li>
  </ul>
  <div class="legal abs">COPYRIGHT 2013. ALL RIGHTS RESERVED.<br>TERMS &amp; CONDITIONS &nbsp;- &nbsp;PRIVACY &nbsp;- &nbsp;&nbsp;DISCLAIMER</div>
  <div class="social abs" aria-label="Social links">
    <span style="background:#5bc1ec"></span>
    <span style="background:#c4302b"></span>
    <span style="background:#3b5a9a"></span>
  </div>

</div>
</body>
</html>
```